Facial Tissue Brand Logo and Design

We would like you to design a Logo for the Facial Tissue Brand "Velora" along with the box design. The pack should indicate the pack size (150 x 2 ply). Also our company logo should be present (attached) along with a barcode. The box size dimensions should be 210mm (L) x 110mm (W) x 70mm (H). We are open to all kinds of nice designs which are attractive but not overdone. Happy designing!

UPDATE:
We appreciate the designs so far... but would also love to see more options in a simple and elegent design style that would look good on a table... please see attached below links for reference purpose:

www.pictovault-example.com/image-photo/cleaning-wipes-isolated-on-white-257770819

www.pictovault-example.com/image-photo/cleaning-wipes-isolated-on-white-155326937

www.pictovault-example.com/image-photo/delicate-female-hands-pulling-tissue-out-1330426586

Happy desgining!

We appreciate the designs so far.. but would like to to see some more options.

```html
<!DOCTYPE html>
<html lang="en">
<head>
<meta charset="utf-8">
<title>Velora Facial Tissue – Identity and Box Dieline</title>
<link href="https://fonts.googleapis.com/css2?family=Michroma&family=Montserrat:wght@400;500;600&display=swap" rel="stylesheet">
<style>
  :root {
    --brand-blue: #0a6d9e;
    --brand-light: #8bbbd9;
    --deep-blue: #0b4f7d;
    --mid-blue: #2a82b8;
    --stage-blue: #b8e4fc;
    --paper: #ffffff;
    --panel-grey: #e6eaee;
    --panel-shade: #cfd6dc;
    --dim-red: #e0465a;
    --fold-line: #9cc4e0;
  }
  * { margin: 0; padding: 0; box-sizing: border-box; }
  html, body { width: 781px; height: 1200px; overflow: hidden; }
  body { position: relative; background: var(--paper); font-family: "Montserrat", sans-serif; }

  .identity { position: absolute; left: 0; top: 0; width: 781px; height: 447px; background: var(--paper); }
  .identity__name {
    position: absolute; left: 0; right: 0; top: 203px; text-align: center;
    font-family: "Michroma", sans-serif; font-size: 30px; letter-spacing: 4px;
    color: var(--brand-blue);
  }

  .dieline-stage { position: absolute; left: 0; top: 447px; width: 781px; height: 753px; background: var(--stage-blue); }

  .panel { position: absolute; }
  .panel--top-face {
    left: 258px; top: 157px; width: 262px; height: 464px; border-radius: 4px 4px 0 0;
    background: linear-gradient(180deg, #0c4f7c 0%, #176fa6 14%, #6fa9cf 26%, #dbe8f1 36%, #f7fafc 48%, #eef4f8 62%, #9fc4dc 72%, #2a82b8 82%, #0d5a8b 100%);
    box-shadow: 0 8px 24px rgba(40,110,160,.25);
  }
  .panel--side {
    width: 94px; border-radius: 4px;
    background: linear-gradient(135deg, #f6f8fa 0%, var(--panel-grey) 45%, #fbfcfd 70%, var(--panel-shade) 100%);
    box-shadow: 0 8px 20px rgba(40,110,160,.2);
  }
  .panel--left-upper  { left: 164px; top: 247px; height: 147px; }
  .panel--right-upper { left: 520px; top: 247px; height: 147px; }
  .panel--left-lower  { left: 164px; top: 472px; height: 147px; }
  .panel--right-lower { left: 520px; top: 472px; height: 147px; }
  .glue-strip { position: absolute; width: 8px; background: var(--panel-shade); }
  .glue-strip--left  { left: 251px; top: 239px; height: 383px; }
  .glue-strip--right { left: 520px; top: 239px; height: 383px; }

  .fold { position: absolute; border-top: 1px dashed var(--fold-line); opacity: .8; }
  .fold--v { border-top: none; border-left: 1px dashed var(--fold-line); }

  .dispenser-opening {
    position: absolute; left: 301px; top: 295px; width: 176px; height: 50px; border-radius: 25px;
    background: rgba(255,255,255,.75); border: 1px dashed var(--fold-line);
  }

  .wordmark { position: absolute; font-family: "Michroma", sans-serif; letter-spacing: 2px; white-space: nowrap; }
  .wordmark--lid { left: 358px; top: 193px; font-size: 12px; color: var(--paper); transform: rotate(180deg); }
  .wordmark--small { left: 275px; top: 361px; font-size: 8px; color: var(--brand-blue); transform: rotate(180deg); }
  .wordmark--main { left: 360px; top: 425px; font-size: 12px; color: var(--brand-blue); }
  .wordmark--end-left  { left: 180px; top: 538px; font-size: 12px; color: var(--brand-blue); transform: rotate(90deg); }
  .wordmark--end-right { left: 532px; top: 538px; font-size: 12px; color: var(--brand-blue); transform: rotate(-90deg); }

  .pack-info { position: absolute; font-size: 5.5px; line-height: 1.3; color: var(--brand-blue); }
  .pack-info strong { display: block; font-weight: 500; font-size: 4.5px; }
  .pack-info--lid-1 { left: 478px; top: 170px; color: var(--paper); transform: rotate(180deg); }
  .pack-info--lid-2 { left: 478px; top: 256px; color: var(--paper); transform: rotate(180deg); }
  .pack-info--front { left: 265px; top: 455px; }

  .company { position: absolute; width: 90px; font-size: 5px; color: var(--brand-blue); white-space: nowrap; }
  .company__name { font-weight: 600; letter-spacing: .5px; }
  .company__line { font-size: 2.6px; letter-spacing: 1px; color: var(--brand-light); margin-top: 2px; }
  .company--left  { left: 188px; top: 315px; transform: rotate(90deg); }
  .company--right { left: 506px; top: 315px; transform: rotate(-90deg); }

  .dimension { position: absolute; border: 1px dashed var(--dim-red); border-radius: 6px; }
  .dimension--length { left: 258px; top: 133px; width: 262px; height: 14px; border-bottom: none; }
  .dimension--height { left: 550px; top: 165px; width: 20px; height: 80px; border-left: none; }
  .dimension--width  { left: 630px; top: 252px; width: 14px; height: 137px; border-left: none; }
  .dimension__label { position: absolute; font-size: 6px; color: var(--dim-red); white-space: nowrap; }
  .dimension__label--length { left: 377px; top: 136px; }
  .dimension__label--height { left: 549px; top: 200px; transform: rotate(90deg); }
  .dimension__label--width  { left: 625px; top: 315px; transform: rotate(90deg); }
</style>
</head>
<body>
  <section class="identity">
    <div class="identity__name">Velora</div>
  </section>

  <section class="dieline-stage">
    <div class="dimension dimension--length"></div>
    <span class="dimension__label dimension__label--length">210 mm</span>
    <div class="dimension dimension--height"></div>
    <span class="dimension__label dimension__label--height">70 mm</span>
    <div class="dimension dimension--width"></div>
    <span class="dimension__label dimension__label--width">110 mm</span>

    <div class="glue-strip glue-strip--left"></div>
    <div class="glue-strip glue-strip--right"></div>

    <div class="panel panel--side panel--left-upper" role="img" aria-label="Pale grey low-poly faceted pattern"></div>
    <div class="panel panel--side panel--right-upper" role="img" aria-label="Pale grey low-poly faceted pattern"></div>
    <div class="panel panel--side panel--left-lower" role="img" aria-label="Pale grey low-poly faceted pattern"></div>
    <div class="panel panel--side panel--right-lower" role="img" aria-label="Pale grey low-poly faceted pattern"></div>
    <div class="panel panel--top-face" role="img" aria-label="Blue to white low-poly faceted pattern across the box wrap"></div>

    <div class="fold" style="left:258px;top:164px;width:262px"></div>
    <div class="fold" style="left:172px;top:240px;width:434px"></div>
    <div class="fold" style="left:172px;top:385px;width:434px"></div>
    <div class="fold" style="left:172px;top:480px;width:434px"></div>
    <div class="fold" style="left:172px;top:611px;width:434px"></div>
    <div class="fold fold--v" style="left:172px;top:251px;height:139px"></div>
    <div class="fold fold--v" style="left:606px;top:251px;height:139px"></div>
    <div class="fold fold--v" style="left:172px;top:476px;height:139px"></div>
    <div class="fold fold--v" style="left:606px;top:476px;height:139px"></div>

    <div class="dispenser-opening"></div>

    <div class="pack-info pack-info--lid-1">Facial Tissue<strong>150 x 2 ply</strong></div>
    <div class="pack-info pack-info--lid-2">Facial Tissue<strong>150 x 2 ply</strong></div>
    <div class="wordmark wordmark--lid">Velora</div>
    <div class="wordmark wordmark--small">Velora</div>
    <div class="wordmark wordmark--main">Velora</div>
    <div class="pack-info pack-info--front">Facial Tissue<strong>150 x 2 ply</strong></div>

    <div class="company company--left">
      <div class="company__name">NORVALE TRADING FZC</div>
      <div class="company__line">quality paper products</div>
    </div>
    <div class="company company--right">
      <div class="company__name">NORVALE TRADING FZC</div>
      <div class="company__line">quality paper products</div>
    </div>

    <div class="wordmark wordmark--end-left">Velora</div>
    <div class="wordmark wordmark--end-right">Velora</div>
  </section>
</body>
</html>
```